IT Services Company - Company Logo, Flyer design

We are an IT professional services company that provides technical service and support in the residential market. I would like to create a colorful logo and flyer that will be mainly letterbox dropped.

Target Market(s)

residential

Industry/Entity Type

It Company

Requirements
Must have
• nice look and feel, easy to read

```html
<!DOCTYPE html>
<html lang="en">
<head>
<meta charset="utf-8">
<title>Brightlink Communications – Flyer</title>
<link href="https://fonts.googleapis.com/css2?family=Lato:ital,wght@0,400;0,700;0,900;1,400;1,700;1,900&family=Oswald:wght@400&display=swap" rel="stylesheet">
<style>
  :root {
    --page-bg: #e6e6e6;
    --ink-dark: #1f1f1f;
    --panel-dark: #262626;
    --brand-blue: #1e9be6;
    --brand-blue-light: #2ab8f7;
    --paper: #f2f2f2;
    --paper-shade: #cfcfcf;
    --white: #ffffff;
    --text-body: #222222;
  }
  * { box-sizing: border-box; margin: 0; padding: 0; }
  html, body { width: 1200px; height: 1200px; overflow: hidden; }
  body { background: var(--page-bg); font-family: 'Lato', sans-serif; position: relative; }

  .flyer {
    position: absolute; left: 180px; top: 56px;
    width: 840px; height: 1088px; overflow: hidden;
    background: var(--white);
  }
  .hero-backdrop {
    position: absolute; left: 0; top: 0; width: 840px; height: 520px;
    background: linear-gradient(180deg, #f4f4f4 0%, #e9e9e9 60%, #f1f1f1 100%);
  }
  .brand { position: absolute; left: 72px; top: 52px; display: flex; align-items: center; gap: 14px; }
  .brand-dot { width: 56px; height: 56px; border-radius: 50%; background: var(--brand-blue); }
  .brand-name { font-weight: 900; font-size: 38px; line-height: 1; color: var(--ink-dark); letter-spacing: -0.5px; }
  .brand-sub { font-weight: 700; font-size: 11px; letter-spacing: 1.6px; color: var(--ink-dark); margin-top: 4px; }

  .intro-frame {
    position: absolute; left: 36px; top: 160px; width: 430px; height: 312px;
    background: var(--brand-blue);
  }
  .intro-panel {
    position: absolute; left: 48px; top: 172px; width: 420px; height: 288px;
    background: linear-gradient(180deg, #333 0%, var(--panel-dark) 55%, #1b1b1b 100%);
    padding: 32px 0 0 45px; color: var(--white);
  }
  .intro-text { width: 250px; font-style: italic; font-size: 21px; line-height: 25.5px; }
  .price { font-family: 'Oswald', sans-serif; font-size: 24px; line-height: 28px; margin-top: 25px; color: var(--brand-blue-light); }
  .cards { font-family: 'Oswald', sans-serif; font-size: 24px; line-height: 28px; }

  .divider { position: absolute; left: 0; top: 512px; width: 470px; height: 8px; background: #333; }

  .services-band {
    position: absolute; left: 0; top: 532px; width: 840px; height: 478px;
    background: linear-gradient(90deg, var(--brand-blue) 0%, var(--brand-blue-light) 55%, var(--brand-blue) 100%);
  }
  .hero-ring { position: absolute; left: 0; top: 0; width: 840px; height: 1088px; pointer-events: none; }

  .service-sheet { position: absolute; left: 42px; top: 575px; width: 412px; height: 387px; }
  .service-list { position: absolute; left: 88px; top: 611px; list-style: none; font-size: 14.3px; color: var(--text-body); }
  .service-list li { position: relative; line-height: 22px; }
  .service-list li svg { position: absolute; left: -21px; top: 5px; }

  .procure, .enquiry, .afterhours {
    position: absolute; color: var(--white); font-weight: 900; font-style: italic;
  }
  .procure { left: 470px; top: 657px; width: 350px; text-align: center; font-size: 18.5px; line-height: 23px; }
  .enquiry { left: 488px; top: 900px; width: 310px; text-align: right; font-size: 15px; line-height: 20px; }
  .afterhours { left: 400px; top: 972px; width: 398px; text-align: right; font-size: 15px; }

  .footer {
    position: absolute; left: 0; top: 1025px; width: 840px; height: 63px;
    background: linear-gradient(180deg, #3a3a3a, #262626);
    color: var(--white); font-size: 16.5px; text-align: center; line-height: 54px; padding-right: 30px;
  }
  .footer-notch { position: absolute; right: 0; top: 1025px; width: 24px; height: 22px; background: var(--white); }
</style>
</head>
<body>
<div class="flyer">
  <div class="hero-backdrop" role="img" aria-label="Faded office photo of colleagues at work"></div>

  <div class="brand">
    <div class="brand-dot"></div>
    <div>
      <div class="brand-name">Brightlink</div>
      <div class="brand-sub">COMMUNICATIONS PTY LTD</div>
    </div>
  </div>

  <div class="intro-frame"></div>
  <div class="intro-panel">
    <p class="intro-text">We are an IT professional services company that provides technical service and support for the North Shore residential market.</p>
    <p class="price">We charge $70 Ex GST per hour</p>
    <p class="cards">All major credit cards accepted</p>
  </div>

  <div class="divider"></div>
  <div class="services-band"></div>

  <svg class="hero-ring" viewBox="0 0 840 1088">
    <defs>
      <linearGradient id="teamPhoto" x1="0" y1="0" x2="1" y2="1">
        <stop offset="0" stop-color="#eef4fa"/>
        <stop offset="0.5" stop-color="#9bb6d3"/>
        <stop offset="1" stop-color="#2c4a72"/>
      </linearGradient>
      <linearGradient id="meetingPhoto" x1="0" y1="0" x2="1" y2="1">
        <stop offset="0" stop-color="#dfe8f1"/>
        <stop offset="1" stop-color="#5d7391"/>
      </linearGradient>
      <linearGradient id="chartPhoto" x1="0" y1="0" x2="1" y2="1">
        <stop offset="0" stop-color="#f4f7fb"/>
        <stop offset="1" stop-color="#a8bdd6"/>
      </linearGradient>
    </defs>
    <circle cx="660" cy="345" r="270" fill="var(--white)"/>
    <circle cx="660" cy="345" r="262" fill="#1e1e1e"/>
    <line x1="560" y1="131" x2="548" y2="106" stroke="var(--white)" stroke-width="10"/>
    <line x1="549" y1="553" x2="536" y2="578" stroke="var(--white)" stroke-width="10"/>
    <circle cx="660" cy="345" r="238" fill="var(--white)"/>
    <circle cx="660" cy="345" r="232" fill="var(--brand-blue-light)"/>
    <circle cx="660" cy="345" r="226" fill="url(#teamPhoto)" role="img" aria-label="Photo of three smiling office workers giving a thumbs up beside a laptop"/>
    <circle cx="568" cy="808" r="74" fill="var(--white)"/>
    <circle cx="568" cy="808" r="70" fill="#1e1e1e"/>
    <circle cx="568" cy="808" r="62" fill="url(#meetingPhoto)" role="img" aria-label="Photo of a business meeting presentation"/>
    <circle cx="728" cy="808" r="74" fill="var(--white)"/>
    <circle cx="728" cy="808" r="70" fill="#1e1e1e"/>
    <circle cx="728" cy="808" r="62" fill="url(#chartPhoto)" role="img" aria-label="Photo of hands reviewing printed charts"/>
  </svg>

  <svg class="service-sheet" viewBox="0 0 412 387">
    <defs>
      <linearGradient id="sheetFill" x1="0" y1="0" x2="1" y2="0">
        <stop offset="0" stop-color="#fafafa"/>
        <stop offset="0.7" stop-color="#f2f2f2"/>
        <stop offset="1" stop-color="#d8d8d8"/>
      </linearGradient>
    </defs>
    <path d="M22 0 H356 L412 38 V387 H0 V20 Z" fill="url(#sheetFill)"/>
    <path d="M356 0 L356 34 L412 38 Z" fill="var(--paper-shade)"/>
  </svg>

  <ul class="service-list">
    <li><svg width="13" height="12" viewBox="0 0 13 12"><circle cx="6" cy="6" r="5.5" fill="var(--brand-blue)"/><path d="M3 6 L5.5 8.5 L12 1.5" stroke="#1a3b66" stroke-width="2" fill="none"/></svg>Home Network &amp; Wireless setup</li>
    <li><svg width="13" height="12" viewBox="0 0 13 12"><circle cx="6" cy="6" r="5.5" fill="var(--brand-blue)"/><path d="M3 6 L5.5 8.5 L12 1.5" stroke="#1a3b66" stroke-width="2" fill="none"/></svg>Improvements for extending your home Wireless</li>
    <li><svg width="13" height="12" viewBox="0 0 13 12"><circle cx="6" cy="6" r="5.5" fill="var(--brand-blue)"/><path d="M3 6 L5.5 8.5 L12 1.5" stroke="#1a3b66" stroke-width="2" fill="none"/></svg>IP Camera installations – external and internal</li>
    <li><svg width="13" height="12" viewBox="0 0 13 12"><circle cx="6" cy="6" r="5.5" fill="var(--brand-blue)"/><path d="M3 6 L5.5 8.5 L12 1.5" stroke="#1a3b66" stroke-width="2" fill="none"/></svg>Backup solutions either at home or to a cloud provider</li>
    <li><svg width="13" height="12" viewBox="0 0 13 12"><circle cx="6" cy="6" r="5.5" fill="var(--brand-blue)"/><path d="M3 6 L5.5 8.5 L12 1.5" stroke="#1a3b66" stroke-width="2" fill="none"/></svg>Computer &amp; Network Security</li>
    <li><svg width="13" height="12" viewBox="0 0 13 12"><circle cx="6" cy="6" r="5.5" fill="var(--brand-blue)"/><path d="M3 6 L5.5 8.5 L12 1.5" stroke="#1a3b66" stroke-width="2" fill="none"/></svg>Email setup</li>
    <li><svg width="13" height="12" viewBox="0 0 13 12"><circle cx="6" cy="6" r="5.5" fill="var(--brand-blue)"/><path d="M3 6 L5.5 8.5 L12 1.5" stroke="#1a3b66" stroke-width="2" fill="none"/></svg>Domain setup and email migration to cloud</li>
    <li><svg width="13" height="12" viewBox="0 0 13 12"><circle cx="6" cy="6" r="5.5" fill="var(--brand-blue)"/><path d="M3 6 L5.5 8.5 L12 1.5" stroke="#1a3b66" stroke-width="2" fill="none"/></svg>StreamCast installations and wireless setup –<br>Stream movies and shows to your existing TV</li>
    <li><svg width="13" height="12" viewBox="0 0 13 12"><circle cx="6" cy="6" r="5.5" fill="var(--brand-blue)"/><path d="M3 6 L5.5 8.5 L12 1.5" stroke="#1a3b66" stroke-width="2" fill="none"/></svg>Computer Setup</li>
    <li><svg width="13" height="12" viewBox="0 0 13 12"><circle cx="6" cy="6" r="5.5" fill="var(--brand-blue)"/><path d="M3 6 L5.5 8.5 L12 1.5" stroke="#1a3b66" stroke-width="2" fill="none"/></svg>New computer recommendations</li>
    <li><svg width="13" height="12" viewBox="0 0 13 12"><circle cx="6" cy="6" r="5.5" fill="var(--brand-blue)"/><path d="M3 6 L5.5 8.5 L12 1.5" stroke="#1a3b66" stroke-width="2" fill="none"/></svg>New computer unpacking and setup</li>
    <li><svg width="13" height="12" viewBox="0 0 13 12"><circle cx="6" cy="6" r="5.5" fill="var(--brand-blue)"/><path d="M3 6 L5.5 8.5 L12 1.5" stroke="#1a3b66" stroke-width="2" fill="none"/></svg>Mobile phone setups and training</li>
    <li><svg width="13" height="12" viewBox="0 0 13 12"><circle cx="6" cy="6" r="5.5" fill="var(--brand-blue)"/><path d="M3 6 L5.5 8.5 L12 1.5" stroke="#1a3b66" stroke-width="2" fill="none"/></svg>Computer training</li>
    <li><svg width="13" height="12" viewBox="0 0 13 12"><circle cx="6" cy="6" r="5.5" fill="var(--brand-blue)"/><path d="M3 6 L5.5 8.5 L12 1.5" stroke="#1a3b66" stroke-width="2" fill="none"/></svg>Telephony &amp; Network Cable relations &amp; installations</li>
  </ul>

  <p class="procure">We can procure all new hardware &amp;<br>provide you obligation free quotes.</p>
  <p class="enquiry">No job is too small, please call or email<br>our team who will be happy to assist with<br>your enquiry &amp; schedule an appointment.</p>
  <p class="afterhours">We can also accommodate afterhours appointments.</p>

  <div class="footer">Ltd ABN - 48 202 615 377 Established 2002 | Call: 123.456.789 | mail: email@website.com</div>
  <div class="footer-notch"></div>
</div>
</body>
</html>
```